New Website for novelty yarn producer

We need a new website for our company, Vedrana. We make highly tailored yarns for weavers worldwide. This year marks our 40th anniversary and we want to evolve our image and identity.

Our temporary website can be found at:
www.vedranathreads.example

Our only concern in that throughout the website the protagonist must be our client, we make their creations possible and are highly adaptable both during the ideation process of the yarn as well as in the production. This is at the core of the way we do business and is summarised within the concept of FMC (Full Motion Craft).

Industry/Entity Type

Textile

Number of Pages Required

1 page

Colors
9bcb3c

Requirements
Must have
• Full Motion Craft (FMC) - can be found on or current website www.vedranathreads.example

```html
<!DOCTYPE html>
<html lang="en">
<head>
<meta charset="utf-8">
<title>Vedrana – Novelty Yarn Solutions</title>
<link rel="stylesheet" href="https://fonts.googleapis.com/css2?family=Lato:wght@300;400;700&family=Lora:wght@400;600&display=swap">
<style>
:root{
  --green:#8cc63f;
  --green-dark:#7db334;
  --green-line:#a3d35f;
  --ink:#1d1d1d;
  --text:#555;
  --muted:#777;
  --grey-bg:#ececec;
  --white:#fff;
  --dark-btn:#222;
}
*{box-sizing:border-box;margin:0;padding:0}
html,body{width:1200px;height:3093px;overflow:hidden;background:var(--white)}
body{position:relative;font-family:'Lato',sans-serif;color:var(--ink)}
.abs{position:absolute}
.btn{position:absolute;display:flex;align-items:center;justify-content:center;background:var(--green);color:var(--white);font-weight:700;font-family:'Lato',sans-serif;border:1px solid #9fd356}

/* header */
.site-header{left:0;top:0;width:1200px;height:107px;background:var(--white)}
.brand{left:95px;top:24px;font-family:'Lora',serif;font-weight:600;font-size:46px;color:var(--ink);letter-spacing:1px}
.main-nav{right:98px;top:42px;display:flex;gap:34px;font-size:16px;color:#666;letter-spacing:.3px}
.main-nav .active{color:var(--ink)}

/* hero */
.hero{left:0;top:107px;width:1200px;height:534px;background:linear-gradient(100deg,#5a3540 0%,#7b4656 35%,#8e2a4c 62%,#b01c52 100%)}
.hero-title{left:0;width:1200px;top:160px;text-align:center;color:var(--white);font-family:'Lora',serif;line-height:1}
.hero-title .l1{display:block;font-size:46px;letter-spacing:1px}
.hero-title .l2{display:block;font-size:60px;margin-top:4px;letter-spacing:1px}
.hero .btn{left:507px;top:291px;width:190px;height:52px;font-size:20px}
.hero-dots{left:553px;top:481px;display:flex;gap:10px}
.hero-dots span{width:15px;height:15px;border-radius:50%;background:var(--white)}
.hero-dots span:first-child{background:transparent;border:2px solid var(--white)}

/* why */
.why{left:0;top:641px;width:1200px;height:452px}
.section-title{width:1200px;left:0;text-align:center;font-size:29px;font-weight:400;letter-spacing:.5px}
.why .section-title{top:50px}
.value{width:304px;height:304px;border-radius:50%;border:3px solid #d8d8d8;top:110px;display:flex;align-items:center;justify-content:center}
.value-inner{width:272px;height:272px;border-radius:50%;background:var(--green);color:var(--white);text-align:center;padding-top:52px}
.value-inner svg{display:block;margin:0 auto 6px}
.value h3{font-size:24px;font-weight:400;margin-bottom:10px}
.value p{font-size:13px;line-height:17px;width:200px;margin:0 auto}

/* about */
.about{left:0;top:1093px;width:1200px;height:484px;background:linear-gradient(90deg,#e7e7e7,#f3f3f3 60%,#f0f0f0)}
.about h2{left:113px;top:92px;font-size:33px;font-weight:400;color:#222}
.about .copy{left:110px;top:145px;width:430px;font-size:15.5px;line-height:27px;color:var(--text)}
.about .copy p+p{margin-top:14px}
.about .btn{left:107px;top:338px;width:157px;height:41px;font-size:17px}
.about-photo{left:588px;top:41px;width:432px;height:402px;border-radius:50%;background:radial-gradient(circle,#f4f4f4 0 22%,#f3a59a 30%,#e56f95 48%,#c78ab8 62%,#f0f0f0 74%)}

/* fmc */
.fmc{left:0;top:1577px;width:1200px;height:361px}
.fmc-mark{left:138px;top:125px;width:104px;height:104px;border-radius:50%;border:4px solid var(--green)}
.fmc-rule{left:277px;top:104px;width:2px;height:146px;background:var(--ink)}
.fmc-name{left:309px;top:123px;font-size:31px;line-height:37px;letter-spacing:.5px;color:var(--ink)}
.fmc h2{left:540px;top:100px;font-size:33px;font-weight:400;color:#222}
.fmc p{left:540px;top:155px;width:540px;font-size:16.5px;line-height:28px;color:var(--text)}
.fmc .btn{left:546px;top:233px;width:172px;height:44px;font-size:17px;background:var(--dark-btn);border-color:var(--dark-btn)}

/* stats */
.stats{left:0;top:1938px;width:1200px;height:165px;background:var(--green)}
.stat{top:24px;width:360px;text-align:center;color:var(--white)}
.stat b{display:block;font-size:66px;font-weight:300;line-height:76px}
.stat span{display:block;font-size:19px;letter-spacing:.3px}

/* blogs */
.blogs{left:0;top:2103px;width:1200px;height:588px}
.blogs .section-title{top:54px;color:var(--green);font-size:35px}
.card{border:2px solid #d8d8d8;background:var(--white)}
.card-img{position:absolute}
.card h4{position:absolute;font-weight:400;font-size:19px;color:#222}
.card p{position:absolute;font-size:13.5px;line-height:20px;color:#888}
.card .btn{font-size:13px;font-weight:700}

/* footer */
.site-footer{left:0;top:2691px;width:1200px;height:336px;background:var(--green);color:var(--white)}
.footer-brand{left:66px;top:80px;font-family:'Lora',serif;font-weight:600;font-size:68px;color:var(--white)}
.footer-col{top:76px}
.footer-col h5{font-size:17px;font-weight:700;letter-spacing:.5px;margin-bottom:20px}
.footer-col li{list-style:none;font-size:17px;line-height:35px}
.footer-rule{top:66px;width:1px;height:181px;background:var(--green-line)}
.socials{left:870px;top:126px;display:flex;gap:8px}
.socials span{width:46px;height:46px;border-radius:50%;border:2px solid var(--white)}
.copyright{left:0;top:3027px;width:1200px;height:66px;background:var(--green-dark);color:var(--white);font-size:15px;text-align:center;line-height:66px}
</style>
</head>
<body>

<header class="abs site-header">
  <div class="abs brand">VEDRANA</div>
  <nav class="abs main-nav">
    <span class="active">HOME</span><span>ABOUT US</span><span>FULL MOTION CRAFT</span><span>TEAM</span><span>BLOG</span><span>CONTACT</span>
  </nav>
</header>

<section class="abs hero" role="img" aria-label="Close-up photograph of mauve and crimson yarn skeins">
  <h1 class="abs hero-title"><span class="l1">BEST TAILORED</span><span class="l2">WEAVING SOLUTIONS</span></h1>
  <a class="btn">Learn More</a>
  <div class="abs hero-dots"><span></span><span></span><span></span><span></span></div>
</section>

<section class="abs why">
  <h2 class="abs section-title">WHY WE ARE</h2>
  <div class="abs value" style="left:130px">
    <div class="value-inner">
      <svg width="60" height="60" viewBox="0 0 60 60" fill="none" stroke="#fff" stroke-width="2.5"><rect x="8" y="12" width="44" height="40" rx="3"/><line x1="8" y1="22" x2="52" y2="22"/><line x1="19" y1="6" x2="19" y2="16"/><line x1="41" y1="6" x2="41" y2="16"/><g fill="#fff" stroke="none"><rect x="14" y="27" width="6" height="5"/><rect x="24" y="27" width="6" height="5"/><rect x="34" y="27" width="6" height="5"/><rect x="14" y="36" width="6" height="5"/><rect x="24" y="36" width="6" height="5"/><rect x="34" y="36" width="6" height="5"/><rect x="14" y="44" width="6" height="4"/><rect x="24" y="44" width="6" height="4"/></g></svg>
      <h3>Experience</h3>
      <p>Over the years the company has gained the knowledge and skills that define the superiority</p>
    </div>
  </div>
  <div class="abs value" style="left:452px">
    <div class="value-inner">
      <svg width="60" height="60" viewBox="0 0 60 60" fill="none" stroke="#fff" stroke-width="2.5"><circle cx="30" cy="26" r="15"/><path d="M23 40v8h14v-8"/><line x1="25" y1="53" x2="35" y2="53"/><line x1="30" y1="3" x2="30" y2="7"/><line x1="9" y1="26" x2="5" y2="26"/><line x1="51" y1="26" x2="55" y2="26"/><line x1="15" y1="11" x2="12" y2="8"/><line x1="45" y1="11" x2="48" y2="8"/></svg>
      <h3>Creativity</h3>
      <p>Our belief is that the key to our clients' success is a combination of innovation, creativity</p>
    </div>
  </div>
  <div class="abs value" style="left:774px">
    <div class="value-inner">
      <svg width="60" height="60" viewBox="0 0 60 60" fill="none" stroke="#fff" stroke-width="2.5"><path d="M6 44c8-6 16-8 24-4h12c3 0 3 4 0 4H30"/><path d="M6 52c10-2 20 0 30-4l18-10c3-2 1-6-2-5l-14 6"/><path d="M30 8l12 12-8 8-12-12z"/><line x1="42" y1="8" x2="48" y2="14"/></svg>
      <h3>Professionality</h3>
      <p>We are a family business at the core. Our company is run with the same values as the Marren</p>
    </div>
  </div>
</section>

<section class="abs about">
  <h2 class="abs">ABOUT VEDRANA</h2>
  <div class="abs copy">
    <p>Our team has decades of experience in providing yarn solutions to weavers around the world, assisting them in the creation of outstanding textiles.</p>
    <p>Our clients can expect open lines of communication, clarity and professionality Our focus is our client. The success of a client is our success.</p>
  </div>
  <a class="btn">Learn More</a>
  <div class="abs about-photo" role="img" aria-label="Photograph of pink, rose and peach yarn balls arranged in a ring"></div>
</section>

<section class="abs fmc">
  <div class="abs fmc-mark"></div>
  <div class="abs fmc-rule"></div>
  <div class="abs fmc-name">FULL<br>MOTION<br>CRAFT</div>
  <h2 class="abs">PRODUCTION BUILT AROUND YOU</h2>
  <p class="abs">Versatility and flexibility both in development and production are key in delivering a custom solution capable of giving life to your products.</p>
  <a class="btn">Find Out More</a>
</section>

<section class="abs stats">
  <svg class="abs" style="left:0;top:0" width="1200" height="165" viewBox="0 0 1200 165"><g stroke="#a9d86a" stroke-width="2"><line x1="456" y1="0" x2="412" y2="165"/><line x1="848" y1="0" x2="804" y2="165"/></g></svg>
  <div class="abs stat" style="left:88px"><b>40</b><span>YEARS IN BUSINESS</span></div>
  <div class="abs stat" style="left:443px"><b>02</b><span>MILLION KILOGRAMS/ YR</span></div>
  <div class="abs stat" style="left:789px"><b>08</b><span>BRANDS</span></div>
</section>

<section class="abs blogs">
  <h2 class="abs section-title">OUR BLOGS</h2>

  <article class="abs card" style="left:87px;top:130px;width:474px;height:363px">
    <div class="card-img" role="img" aria-label="Photograph of colourful yarn cones" style="left:0;top:0;width:470px;height:215px;background:linear-gradient(100deg,#e0307a,#d94a2a 30%,#2aa39a 55%,#8db63c 75%,#d5d0c4)"></div>
    <h4 style="left:25px;top:232px">Maecenas at justo id velit placerat</h4>
    <p style="left:25px;top:262px;width:420px">netus et malesuada fames ac turpis egestas Cras id elit Integer quis urna Ut ante enim dapibus malesuada fringilla eu condimen</p>
    <a class="btn" style="left:25px;top:309px;width:124px;height:33px">READ MORE</a>
  </article>

  <article class="abs card" style="left:577px;top:130px;width:528px;height:177px">
    <div class="card-img" role="img" aria-label="Photograph of golden orange yarn" style="left:0;top:0;width:256px;height:173px;background:linear-gradient(120deg,#b8680f,#e29a2a 50%,#c0741a)"></div>
    <h4 style="left:283px;top:25px">News Title here</h4>
    <p style="left:283px;top:55px;width:230px">netus et malesuada fames ac turpis egestas Cras id elit Integer quis urna Ut ante enim dapibus malesuada</p>
    <a class="btn" style="left:283px;top:126px;width:124px;height:31px">READ MORE</a>
  </article>

  <article class="abs card" style="left:577px;top:316px;width:528px;height:177px">
    <div class="card-img" role="img" aria-label="Photograph of purple yarn cones with green thread" style="left:0;top:0;width:256px;height:173px;background:linear-gradient(160deg,#5d7a30,#4a2235 40%,#7a2c5c 75%,#3a1a2a)"></div>
    <h4 style="left:283px;top:25px">News Title here</h4>
    <p style="left:283px;top:55px;width:230px">netus et malesuada fames ac turpis egestas Cras id elit Integer quis urna Ut ante enim dapibus malesuada</p>
    <a class="btn" style="left:283px;top:126px;width:124px;height:31px">READ MORE</a>
  </article>
</section>

<footer class="abs site-footer">
  <div class="abs footer-brand">VEDRANA</div>
  <div class="abs footer-col" style="left:394px">
    <h5>QUICK LINKS</h5>
    <ul><li>Home</li><li>About Us</li><li>Full Motion Craft</li><li>Why Us</li></ul>
  </div>
  <div class="abs footer-rule" style="left:631px"></div>
  <div class="abs footer-col" style="left:670px">
    <h5>RESOURCES</h5>
    <ul><li>Blog</li><li>Term of Use</li><li>Contact Us</li></ul>
  </div>
  <div class="abs footer-rule" style="left:835px"></div>
  <div class="abs footer-col" style="left:872px">
    <h5>FOLLOW US</h5>
  </div>
  <div class="abs socials" aria-label="Social media links"><span></span><span></span><span></span><span></span></div>
</footer>

<div class="abs copyright">© 2018 Company Name &nbsp;All right reserved</div>

</body>
</html>
```